Presentation Folder, for Cancer Awareness, VERY COLORFULL AND MODERN

This will be a standard size folder that will hold standard 8 1/2 x 11 papers with a business card slot on the flap, this is a very easy project with very little text and the design for the back page is already done so all you really have to do is make a very nice colorful front cover, you will see my attachments are labeled and I gave you alot of instructions, this should be a very fast easy project
Updates

Reason: there has not been enough quality designs, sorry

Target Market(s)

Our Target Market is Dr's that Deal with Cancer patients

Industry/Entity Type

Healthcare

Font styles to use
Serif

Colors

Designer to choose colors to be used in the design.

Requirements
Must have
• Project must be tasteful and look professional with the ribbons as the main focal point in the center of folder the folder should be a nice gray color to accent the color of the ribbons , the back page needs no design it is the" Sorvane Test" in the attachments I sent
Nice to have
• I would like the ribbons displayed in a row, I included a logo sample layout
• a picture on the front of the folder under the words Hereditary Cancer Screening - Then under that put the words - The Power of Knowledge - then add the picture I labeled Great Picture in the attachments

```html
<!DOCTYPE html>
<html lang="en">
<head>
<meta charset="utf-8">
<title>Hereditary Cancer Screening Folder</title>
<link href="https://fonts.googleapis.com/css2?family=Arimo:wght@400;700&family=Josefin+Sans:wght@300;400&family=Questrial&display=swap" rel="stylesheet">
<style>
  :root {
    --red: #e8312c;
    --gene-red: #e03a2a;
    --pink: #e61d74;
    --ink: #1b1b1b;
    --grey-text: #8a8a8a;
    --row-alt: #efefef;
    --lynch: #fcc33d;
    --pj: #a9c43f;
    --lf: #3daf57;
    --cowden: #1a9ad7;
    --hdgc: #6b6b66;
    --paper: #ffffff;
  }
  * { box-sizing: border-box; margin: 0; padding: 0; }
  html, body { width: 1200px; height: 800px; overflow: hidden; background: var(--paper); }
  .folder { position: relative; width: 1200px; height: 800px; font-family: "Arimo", Arial, sans-serif; color: var(--ink); }

  /* Back page: test menu */
  .back-page { position: absolute; left: 0; top: 0; width: 600px; height: 800px; }
  .brand-name { position: absolute; left: 32px; top: 44px; font-family: "Josefin Sans", sans-serif; font-weight: 300; font-size: 22px; letter-spacing: 7px; color: var(--red); }
  .brand-contact { position: absolute; left: 32px; top: 73px; font-size: 5.6px; letter-spacing: 0.6px; line-height: 9px; color: #444; text-transform: uppercase; }
  .brand-contact .lower { text-transform: none; }
  .menu-title { position: absolute; right: 53px; top: 44px; font-size: 21px; font-weight: 700; color: var(--red); }
  .menu-title sup { font-size: 7px; vertical-align: 12px; }
  .lab-id { position: absolute; right: 53px; top: 83px; font-size: 5.6px; letter-spacing: 0.6px; color: #555; }
  .lab-id b { letter-spacing: 1px; }

  .gene-table { position: absolute; left: 133px; top: 108px; width: 318px; border-collapse: collapse; font-size: 7.8px; }
  .gene-table td { height: 15.85px; padding: 0; vertical-align: middle; }
  .gene-table .gene { width: 100px; padding-left: 6px; color: var(--gene-red); font-weight: 700; letter-spacing: 0.6px; }
  .gene-table .organ { font-weight: 700; color: #333; font-size: 7.6px; }
  .gene-table .indent { padding-left: 15px; }
  .gene-table tr.alt td { background: var(--row-alt); }
  .gene-table tr.head td { background: var(--red); color: #fff; font-weight: 400; letter-spacing: 0.6px; }
  .gene-table tr.band td { color: #fff; letter-spacing: 0.7px; padding-left: 15px; font-weight: 400; }
  .band.lynch td { background: var(--lynch); }
  .band.pj td { background: var(--pj); }
  .band.lf td { background: var(--lf); }
  .band.cowden td { background: var(--cowden); }
  .band.hdgc td { background: var(--hdgc); }
  .site-url { position: absolute; left: 164px; top: 767px; font-family: "Josefin Sans", sans-serif; font-size: 11px; letter-spacing: 7px; color: #555; }

  /* Front cover */
  .front-cover { position: absolute; left: 600px; top: 0; width: 600px; height: 800px; }
  .cover-photo { position: absolute; left: 0; top: 0; }
  .cover-title { position: absolute; right: 40px; top: 76px; text-align: right; font-family: "Questrial", sans-serif; font-size: 38px; line-height: 42px; color: var(--pink); }
  .cover-tagline { position: absolute; right: 40px; top: 168px; font-size: 23px; font-weight: 700; color: #000; letter-spacing: 0.3px; }
  .ribbon-row { position: absolute; left: 250px; top: 290px; width: 318px; height: 165px; border-radius: 8px;
    background: linear-gradient(90deg, #f7d31b, #c9c9c9, #ef4f86, #4fcbc0, #a9d3f2, #b75ab0, #2a48a8, #d3a03a); opacity: 0.85; }
  .cancer-list { position: absolute; left: 0; width: 600px; top: 549px; text-align: center; font-family: "Questrial", sans-serif; font-size: 16px; line-height: 22px; color: var(--grey-text); }
  .cover-brand { position: absolute; left: 0; width: 600px; top: 636px; text-align: center; }
  .cover-brand .mark { display: block; width: 34px; height: 34px; margin: 0 auto 12px; border-radius: 50%; background: var(--red); }
  .cover-brand .name { font-family: "Josefin Sans", sans-serif; font-weight: 300; font-size: 18px; letter-spacing: 7px; color: var(--red); }
  .cover-promise { position: absolute; left: 0; width: 600px; top: 735px; text-align: center; font-size: 19px; font-weight: 700; color: var(--red); letter-spacing: 0.3px; }
  .cover-promise .sep { margin: 0 8px; }
</style>
</head>
<body>
<div class="folder">

  <section class="back-page">
    <div class="brand-name">CLARIGENE</div>
    <div class="brand-contact">220 Meridian Park Way | Suite B | Harlow, GA 30999<br><span class="lower">(tel) 555.014.2210 | (fax) 555.014.2211 | cs@clarigene-lab.com</span></div>
    <h1 class="menu-title">SORVANE<sup>™</sup> Test Menu</h1>
    <div class="lab-id">CLIA# 00D0000000 | <b>CLARIGENE-LAB.COM</b></div>

    <table class="gene-table">
      <tr class="head"><td class="gene">GENE</td><td>CANCER-ASSOCIATED ORGAN/SYSTEMS</td></tr>
      <tr><td class="gene">APC</td><td class="organ">Colon</td></tr>
      <tr class="alt"><td class="gene">ATM</td><td class="organ">Breast/Pancreatic/Brain</td></tr>
      <tr><td class="gene">BARD1</td><td class="organ">Breast/Ovarian</td></tr>
      <tr class="alt"><td class="gene">BMPR1A</td><td class="organ">Colon</td></tr>
      <tr><td class="gene">BRCA1</td><td class="organ">Breast/Ovarian/Prostate</td></tr>
      <tr class="alt"><td class="gene">BRCA2</td><td class="organ">Breast/Ovarian/Prostate</td></tr>
      <tr><td class="gene">BRIP1</td><td class="organ">Breast/Ovarian</td></tr>
      <tr class="alt"><td class="gene">CDK4</td><td class="organ">Melanoma</td></tr>
      <tr><td class="gene">P16 (CDKN2A)</td><td class="organ">Melanoma/Breast/Pancreatic/Squamous</td></tr>
      <tr class="alt"><td class="gene">FANCC</td><td class="organ">Blood</td></tr>
      <tr><td class="gene">MEN1</td><td class="organ">Thyroid/Parathyroid</td></tr>
      <tr class="alt"><td class="gene">MET</td><td class="organ">Renal/Hepatic</td></tr>
      <tr><td class="gene">MRE11A</td><td class="organ">Ovarian/Breast</td></tr>
      <tr class="alt"><td class="gene">NBN</td><td class="organ">Breast/Ovarian/Prostate/Melanoma</td></tr>
      <tr><td class="gene">NF1</td><td class="organ">Blood</td></tr>
      <tr class="alt"><td class="gene">NTRK1</td><td class="organ">Thyroid/Parathyroid</td></tr>
      <tr><td class="gene">PALB2</td><td class="organ">Breast/Ovarian/Pancreatic</td></tr>
      <tr class="alt"><td class="gene">PTCH1</td><td class="organ">Melanoma/Brain/Breast/Colon</td></tr>
      <tr><td class="gene">RAD50</td><td class="organ">Breast/Ovarian</td></tr>
      <tr class="alt"><td class="gene">RAD51C</td><td class="organ">Ovarian/Breast</td></tr>
      <tr><td class="gene">RAD51D</td><td class="organ">Ovarian/Breast</td></tr>
      <tr class="alt"><td class="gene">RET</td><td class="organ">Lung/Thyroid/Parathyroid</td></tr>
      <tr><td class="gene">SMAD4</td><td class="organ">Colon/Pancreas</td></tr>
      <tr class="band lynch"><td colspan="2">LYNCH SYNDROME GENES</td></tr>
      <tr><td class="gene indent">MLH1</td><td class="organ">Colorectal/Ovarian</td></tr>
      <tr class="alt"><td class="gene indent">MSH2</td><td class="organ">Colorectal/Ovarian</td></tr>
      <tr><td class="gene indent">MSH6</td><td class="organ">Colorectal/Ovarian</td></tr>
      <tr class="alt"><td class="gene indent">PMS2</td><td class="organ">Colorectal/Ovarian</td></tr>
      <tr><td class="gene indent">EPCAM</td><td class="organ">Colorectal</td></tr>
      <tr class="band pj"><td colspan="2">PEUTZ-JEGHERS SYNDROME GENE</td></tr>
      <tr><td class="gene indent">STK11</td><td class="organ">Breast/Ovarian/Melanoma/Colorectal/Lung</td></tr>
      <tr class="band lf"><td colspan="2">LI-FRAUMENI SYNDROME GENE</td></tr>
      <tr><td class="gene indent">CHEK2</td><td class="organ">Breast/Ovarian/Prostate</td></tr>
      <tr class="alt"><td class="gene indent">PT53</td><td class="organ">Breast/Bladder/Ovarian/Squamous</td></tr>
      <tr class="band cowden"><td colspan="2">COWDEN SYNDROME GENE</td></tr>
      <tr><td class="gene indent">PTEN</td><td class="organ">Endometrium/Breast/Prostate/Lung</td></tr>
      <tr class="band hdgc"><td colspan="2">HEREDITARY DIFFUSE GASTRIC CANCER SYNDROME GENE</td></tr>
      <tr class="alt"><td class="gene indent">CDH1</td><td class="organ">Breast/Gastric/Ovarian/Prostate</td></tr>
      <tr><td class="gene indent">VHL</td><td class="organ">Renal</td></tr>
    </table>

    <div class="site-url">www.clarigene-lab.com</div>
  </section>

  <section class="front-cover">
    <svg class="cover-photo" width="600" height="540" viewBox="0 0 600 540" role="img" aria-label="Photograph of a smiling couple embracing on a bright beach with sky and dune grass">
      <defs>
        <linearGradient id="photoTone" x1="0" y1="0" x2="1" y2="1">
          <stop offset="0" stop-color="#c98a5e"/>
          <stop offset="0.35" stop-color="#d9c2ae"/>
          <stop offset="0.7" stop-color="#e4eaee"/>
          <stop offset="1" stop-color="#b8c7a0"/>
        </linearGradient>
      </defs>
      <path d="M0 0 H600 V500 Q420 520 270 530 Q120 520 0 455 Z" fill="url(#photoTone)"/>
    </svg>

    <h2 class="cover-title">Hereditary Cancer<br>Screening</h2>
    <div class="cover-tagline">The Power of Knowledge</div>
    <div class="ribbon-row" role="img" aria-label="Two rows of awareness ribbons in many cancer colours"></div>

    <p class="cancer-list">Breast, Ovarian, Endometrial, Gastric,<br>Colorectal, Pancreatic, Melanoma, Prostate, lung, Colon</p>

    <div class="cover-brand"><span class="mark"></span><span class="name">CLARIGENE</span></div>

    <div class="cover-promise">Fast<span class="sep">|</span>Comprehensive<span class="sep">|</span>Easy</div>
  </section>

</div>
</body>
</html>
```